Real Estate Company Looking for Business Card Designs for 3 Executives

Hello!
Thanks so much for considering our project! We are a real estate investment company located in Edmonton, Alberta called Bellhaven Group of Companies. We invest/develop both commercial and residential real estate and are looking to create 3 DOUBLE-SIDED business cards for 3 top executives in the company! (for some reason it won't let us select the double-sided option, but yes, the cards are double sided and would be happy to tip extra)

We have certain guidelines that we want our business cards to for sure follow - the back of the Business card has to be the Black Background Version of the Logo which has already been designed and linked as a file (first file). We want the entire back of the card to simply just be the black background logo. In terms of the front of the card, would like to see a smaller version of the white background logo (linked as the second file) in the top left hand corner - of course, feel free to get creative and we can make revisions together along the way! and Then after that, just text. We want the card to be sharp, clean, easy on the eyes and highly professional looking. We would like the card to include the Full name of the Company (Bellhaven Group of Companies), Name of the Person, Title, Phone, Email. If possible please provide the front part of the card for 3 people:

1) Bellhaven Group of Companies, Liora Quenby, Chief Financial Officer, 780-555-0142, lioraquenby@bellhavengroup.example

2) Bellhaven Group of Companies, Tobias Quenby, Chief Executive Officer, 780-555-0187, tobiasquenby@bellhavengroup.example

3) Bellhaven Group of Companies, Rui Delcourt, Chief Operations Officer, 587-555-0163, ruidelcourt@bellhavengroup.example

Thank you so much for considering our project & we look forward to seeing your designs!

```html
<!DOCTYPE html>
<html lang="en">
<head>
<meta charset="utf-8">
<title>Bellhaven Business Card</title>
<link rel="stylesheet" href="https://fonts.googleapis.com/css2?family=Montserrat:wght@400;500;700&display=swap">
<style>
  :root {
    --ink: #0b0809;
    --paper: #ffffff;
    --backdrop: #e9e7e4;
  }
  html, body {
    margin: 0;
    padding: 0;
    width: 1200px;
    height: 900px;
    overflow: hidden;
    background: var(--backdrop);
    font-family: "Montserrat", Arial, sans-serif;
  }
  .canvas {
    position: relative;
    width: 1200px;
    height: 900px;
  }
  .card {
    position: absolute;
    left: 250px;
    width: 700px;
    height: 400px;
    box-shadow: 0 4px 14px rgba(0,0,0,0.18);
    overflow: hidden;
  }
  .card-back {
    top: 35px;
    background: var(--ink);
    display: flex;
    align-items: center;
    justify-content: center;
  }
  .card-front {
    top: 465px;
    background: var(--paper);
  }
  .wordmark {
    display: flex;
    align-items: center;
    gap: 14px;
    font-weight: 500;
    letter-spacing: 0.32em;
    text-transform: uppercase;
  }
  .wordmark-mark {
    display: block;
    background: currentColor;
  }
  .card-back .wordmark {
    color: var(--paper);
    font-size: 40px;
  }
  .card-back .wordmark-mark {
    width: 34px;
    height: 34px;
  }
  .brand-block {
    position: absolute;
    top: 80px;
    right: 40px;
    color: var(--ink);
    text-align: right;
  }
  .card-front .wordmark {
    font-size: 22px;
    gap: 10px;
    justify-content: flex-end;
  }
  .card-front .wordmark-mark {
    width: 20px;
    height: 20px;
  }
  .company-name {
    margin: 8px 0 0;
    font-size: 12px;
    font-weight: 500;
    letter-spacing: 0.12em;
    text-transform: uppercase;
  }
  .holder {
    position: absolute;
    top: 88px;
    left: 44px;
    color: var(--ink);
  }
  .holder-name {
    margin: 0;
    font-size: 27px;
    font-weight: 700;
    letter-spacing: 0.01em;
    text-transform: uppercase;
    line-height: 1.1;
  }
  .holder-title {
    margin: 2px 0 0;
    font-size: 19px;
    font-weight: 400;
  }
  .contact {
    position: absolute;
    left: 44px;
    top: 200px;
    margin: 0;
    padding: 0;
    list-style: none;
    color: var(--ink);
    font-size: 18px;
    line-height: 1.4;
  }
  .contact li {
    display: flex;
    align-items: center;
    gap: 8px;
  }
  .contact svg {
    width: 16px;
    height: 16px;
    flex: none;
  }
  .wave {
    position: absolute;
    left: 0;
    bottom: 0;
    width: 700px;
    height: 400px;
  }
  .website {
    position: absolute;
    right: 36px;
    bottom: 80px;
    color: var(--paper);
    font-size: 17px;
    transform: rotate(-10deg);
    transform-origin: right bottom;
  }
</style>
</head>
<body>
<main class="canvas">
  <section class="card card-back" aria-label="Card back">
    <div class="wordmark"><span class="wordmark-mark"></span>Bellhaven</div>
  </section>

  <section class="card card-front" aria-label="Card front">
    <svg class="wave" viewBox="0 0 700 400" aria-hidden="true">
      <path d="M0,345 C250,338 420,320 520,270 C600,230 650,200 700,196 L700,400 L0,400 Z" fill="var(--ink)"/>
      <path d="M0,366 C250,360 430,338 530,285 C560,268 585,256 600,250" fill="none" stroke="var(--paper)" stroke-width="3"/>
    </svg>

    <div class="brand-block">
      <div class="wordmark"><span class="wordmark-mark"></span>Bellhaven</div>
      <p class="company-name">Bellhaven Group of Companies</p>
    </div>

    <div class="holder">
      <h1 class="holder-name">Liora Quenby</h1>
      <p class="holder-title">Chief Financial Officer</p>
    </div>

    <ul class="contact">
      <li>
        <svg viewBox="0 0 24 24" aria-hidden="true"><path fill="var(--ink)" d="M6.6 10.8a15.1 15.1 0 0 0 6.6 6.6l2.2-2.2a1 1 0 0 1 1-.25 11.4 11.4 0 0 0 3.6.57 1 1 0 0 1 1 1V20a1 1 0 0 1-1 1A17 17 0 0 1 3 4a1 1 0 0 1 1-1h3.5a1 1 0 0 1 1 1c0 1.25.2 2.45.57 3.57a1 1 0 0 1-.25 1z"/></svg>
        780-555-0142
      </li>
      <li>
        <svg viewBox="0 0 24 24" aria-hidden="true"><path fill="var(--ink)" d="M2 5h20v14H2z"/><path fill="none" stroke="var(--paper)" stroke-width="1.6" d="M2.5 5.5 12 13l9.5-7.5"/></svg>
        lioraquenby@bellhavengroup.example
      </li>
    </ul>

    <div class="website">www.bellhavengroup.example</div>
  </section>
</main>
</body>
</html>
```